Buch-/E-Book-Cover für Buch über die Ausdrucksweise
Zielgruppe
Deutsche Version
Ich bin Autor und habe ich Buch über 'Ausdrucksweise verbessern' geschrieben. Das Buch steht aktuell zum Verkauf. Allerdings gefällt mir das Cover nicht gut. Deswegen möchte ich gerne ein neues Cover erstellen lassen. Der Haupttitel lautet 'Worte wirken weiter' und der Untertitel: 'Klarer reden & Sprachgefühl stärken: Das Übungsbuch mit anschaulichen Fällen, wie Sie in jeder Unterhaltung mit Redekunst und Stilsicherheit' Autor ist 'Jonas Brettfeld'
English Version
I am an author and I have written a book on 'Improving Expression'. The book is currently for sale. However, I don't like the cover very much. Therefore, I would like to have a new cover created. The main title is 'Words carry further = Worte wirken weiter' and the subtitle is: 'Speak clearly & sharpen your style: The hands-on workbook with vivid cases showing how to apply eloquence and verbal confidence in every discussion' = 'Klarer reden & Sprachgefühl stärken: Das Übungsbuch mit anschaulichen Fällen, wie Sie in jeder Unterhaltung mit Redekunst und Stilsicherheit'. Author is 'Jonas Brettfeld'.
Aufgabenstellung
Ich habe das aktuelle Cover beigefügt. Mir gefällt die Symbolik des aktuellen Covers noch nicht. Ich denke mit dem Titel 'Worte wirken weiter' kann man noch mehr herausholen, indem man eine bessere Symbolik verwendet. Wichtig ist, dass der potenzielle Kunde sofort die Symbolik mit dem Inhalt assoziiert.
Die Konkurrenzbücher auf Lesora können gute Hinweise sein. Allerdings sollte das neue Cover hier explizit herausstechen: https://www.lesora-shop.de/s?k=ausdrucksweise+verbessern&i=stripbooks&sprefix=ausdrucksw%2Cstripbooks%2C77&ref=nb_sb_ss_ts-doa-p_1_10
Folgende Punkte sind wichtig:
- Haupttitel muss gut lesbar sein. (Untertitel ist unwichtig)
- 'Praxisguide' sollte herausstechen
- Es sollte erkenntlich gemacht werden, dass das Buch ein Hörbuch enthält
Ich habe die Covervorlage mit dem passendem Format hinzugefügt.
English Version:
I have attached the current cover. I don't like the symbolism of the current cover yet. I think with the title 'Words carry further' you can get more out of it by using better symbolism. It is important that the potential customer immediately associates the symbolism with the content.
Competitor books on Lesora can be good clues. However, the new cover should explicitly stand out here: https://www.lesora-shop.de/s?k=ausdrucksweise+improve&i=stripbooks&sprefix=expressionsw%2Cstripbooks%2C77&ref=nb_sb_ss_ts-doa-p_1_10
The following points are important:
- Main title must be easy to read. (Subtitle is not important).
- The cover and the title must be recognizable even in very small format (thumb size - see lesora)
- 'Praxisguide should stand out
- It should be made recognizable that the book contains an audio book 'Inkl.Hörbuch'
I have added the cover template with the appropriate format.

```html
<!DOCTYPE html>
<html lang="de">
<head>
<meta charset="utf-8">
<title>Worte wirken weiter – Jonas Brettfeld</title>
<link rel="stylesheet" href="https://fonts.googleapis.com/css2?family=Caveat+Brush&family=Oswald:wght@400;500&family=Montserrat:wght@400&family=Caveat:wght@700&display=swap">
<style>
  :root {
    --paper: #ffffff;
    --red: #d8303a;
    --coral: #e4574f;
    --plum: #862a7e;
    --night: #3a1440;
    --orange: #f0a224;
    --amber: #ee7a34;
    --band: #0c0c0c;
    --white: #ffffff;
    --lilac: #eadcf0;
  }
  html, body {
    margin: 0;
    padding: 0;
    width: 847px;
    height: 1200px;
    overflow: hidden;
    background: var(--paper);
  }
  .cover {
    position: relative;
    width: 847px;
    height: 1200px;
    overflow: hidden;
    background: var(--paper);
  }
  .backdrop {
    position: absolute;
    inset: 0;
    background:
      linear-gradient(160deg, var(--night) 0%, var(--plum) 22%, var(--red) 48%, var(--coral) 66%, var(--amber) 82%, var(--orange) 100%);
  }
  .title {
    position: absolute;
    right: 30px;
    top: 4px;
    margin: 0;
    text-align: right;
    font-family: "Caveat Brush", cursive;
    font-weight: 400;
    color: var(--white);
    line-height: 1;
  }
  .title .big { display: block; font-size: 150px; letter-spacing: 1px; }
  .title .small { display: block; font-size: 80px; margin: -16px 70px -12px 0; }
  .author {
    position: absolute;
    left: 216px;
    top: 314px;
    margin: 0;
    font-family: "Montserrat", sans-serif;
    font-size: 25px;
    letter-spacing: 1px;
    color: var(--lilac);
  }
  .subtitle {
    position: absolute;
    left: 206px;
    top: 362px;
    width: 330px;
    margin: 0;
    text-align: center;
    font-family: "Oswald", sans-serif;
    font-weight: 500;
    font-size: 46px;
    line-height: 52px;
    color: var(--white);
  }
  .figures {
    position: absolute;
    left: 502px;
    top: 392px;
    width: 320px;
    height: 482px;
    background: linear-gradient(180deg, rgba(255,255,255,0.30), rgba(255,255,255,0.12));
    border-radius: 6px;
  }
  .guide-band {
    position: absolute;
    left: 0;
    top: 983px;
    width: 847px;
    height: 152px;
    background: var(--band);
  }
  .guide-label {
    position: absolute;
    left: 114px;
    top: 995px;
    margin: 0;
    font-family: "Oswald", sans-serif;
    font-weight: 500;
    font-size: 70px;
    line-height: 1;
    letter-spacing: 2px;
    color: var(--white);
  }
  .tagline {
    position: absolute;
    left: 0;
    top: 1090px;
    width: 847px;
    margin: 0;
    text-align: center;
    font-family: "Oswald", sans-serif;
    font-weight: 400;
    font-size: 21px;
    color: var(--white);
  }
  .headphones {
    position: absolute;
    left: 640px;
    top: 925px;
    width: 176px;
    height: 150px;
    border-radius: 80px 80px 20px 20px;
    background: linear-gradient(180deg, rgba(255,255,255,0.22), rgba(255,255,255,0.06));
  }
  .audio-note {
    position: absolute;
    left: 664px;
    top: 1012px;
    margin: 0;
    font-family: "Caveat", cursive;
    font-weight: 700;
    font-size: 32px;
    line-height: 0.9;
    color: var(--white);
    transform: rotate(8deg);
    text-align: center;
  }
</style>
</head>
<body>
<main class="cover">
  <div class="backdrop" role="img" aria-label="Abstraktes Muster aus überlagerten Kreisen und Bändern in Rot, Violett und Orange"></div>

  <h1 class="title">
    <span class="big">Worte</span>
    <span class="small">wirken</span>
    <span class="big">weiter</span>
  </h1>

  <p class="author">Jonas Brettfeld</p>

  <h2 class="subtitle">Klarer reden &amp; Sprachgefühl stärken</h2>

  <div class="figures" role="img" aria-label="Strichzeichnung von drei Personen im Gespräch mit Getränken in der Hand"></div>

  <div class="guide-band"></div>
  <p class="guide-label">Das Übungsbuch</p>
  <p class="tagline">mit anschaulichen Fällen, wie Sie in jeder Unterhaltung mit Redekunst und Stilsicherheit überzeugen</p>

  <div class="headphones" role="img" aria-label="Gezeichnete Kopfhörer mit Kabel als Hinweis auf das Hörbuch"></div>
  <p class="audio-note">mit<br>Hörbuch</p>
</main>
</body>
</html>
```